Whitcombe Business Card Design

The name of the business is Dario Whitcombe, CPA LLC
The service that we offer is Accounting, Tax & Consulting Services. I need it to have the following items:
Dario Whitcombe, Principal
Phone Number
Email Address
Physical Address

I have attached the company logo, one in black and one in white. Please provide a design in black background and the other in white background. Please include "Accounting, Tax & Consulting Services". I want the business card to be clean and very professional.

```html
<!DOCTYPE html>
<html lang="en">
<head>
<meta charset="utf-8">
<title>Dario Whitcombe, CPA LLC — Business Cards</title>
<link rel="stylesheet" href="https://fonts.googleapis.com/css2?family=Nunito+Sans:wght@400;600;700&display=swap">
<style>
  :root {
    --backdrop: #1e1e1f;
    --card: #e9eaeb;
    --red: #9d1c22;
    --red-bright: #b0262d;
    --charcoal: #3b3c3e;
    --ink: #3d3d3f;
    --grey: #8a8b8d;
    --white: #ffffff;
  }
  * { margin: 0; padding: 0; box-sizing: border-box; }
  html, body { width: 1200px; height: 1200px; overflow: hidden; }
  body {
    background: var(--backdrop);
    font-family: "Nunito Sans", "Helvetica Neue", Arial, sans-serif;
    position: relative;
  }
  .card {
    position: absolute;
    left: 228px;
    width: 744px;
    height: 430px;
    background: var(--card);
    overflow: hidden;
  }
  .card--front { top: 145px; }
  .card--back { top: 640px; }

  .card__shapes { position: absolute; inset: 0; }

  /* Front */
  .name-banner {
    position: absolute;
    left: 45px;
    top: 70px;
    color: var(--white);
  }
  .name-banner__name {
    font-size: 22px;
    font-weight: 400;
    letter-spacing: 0.5px;
    text-transform: uppercase;
    line-height: 1.1;
  }
  .name-banner__name strong { font-weight: 700; }
  .name-banner__role { font-size: 16px; margin-top: 4px; }

  .firm-mark {
    position: absolute;
    right: 30px;
    top: 72px;
    text-align: right;
    color: var(--white);
  }
  .firm-mark__name {
    font-size: 18px;
    font-weight: 600;
    letter-spacing: 0.3px;
    text-transform: uppercase;
  }
  .firm-mark__tagline {
    font-size: 12px;
    font-weight: 600;
    letter-spacing: 1.2px;
    text-transform: uppercase;
    margin-top: 2px;
  }

  .contact {
    position: absolute;
    left: 92px;
    color: var(--ink);
    font-size: 12.5px;
    line-height: 1.25;
  }
  .contact--phone { top: 245px; }
  .contact--email { top: 300px; }
  .contact--web { top: 344px; }

  /* Back */
  .firm-lockup {
    position: absolute;
    left: 0;
    right: 0;
    top: 200px;
    text-align: center;
  }
  .firm-lockup__name {
    font-size: 27px;
    font-weight: 600;
    color: var(--ink);
    text-transform: uppercase;
    letter-spacing: 0.5px;
  }
  .firm-lockup__tagline {
    font-size: 16px;
    font-weight: 600;
    color: var(--grey);
    letter-spacing: 1.8px;
    text-transform: uppercase;
    margin-top: 2px;
  }
  .services {
    position: absolute;
    left: 0;
    right: 0;
    top: 374px;
    text-align: center;
    color: var(--red);
    font-size: 23px;
    font-weight: 400;
  }
</style>
</head>
<body>

<section class="card card--front" aria-label="Business card front">
  <svg class="card__shapes" width="744" height="430" viewBox="0 0 744 430" aria-hidden="true">
    <polygon points="0,62 291,62 266,129 0,129" fill="var(--red)"/>
    <polygon points="422,0 364,134 504,430 744,430 744,0" fill="var(--red-bright)"/>
    <polygon points="440,0 372,136 504,430 540,430 398,140 462,0" fill="var(--red)"/>
    <polygon points="462,0 398,140 538,430 744,430 744,0" fill="var(--charcoal)"/>
    <line x1="0" y1="281" x2="304" y2="281" stroke="var(--red)" stroke-width="1.2"/>
    <line x1="0" y1="332" x2="304" y2="332" stroke="var(--red)" stroke-width="1.2"/>
    <!-- phone icon -->
    <circle cx="60" cy="259" r="15" fill="var(--red)"/>
    <path d="M54 252 c1-1 3-1 4 0 l2 3 c0 1 0 2-1 2 l-1 1 c1 2 3 4 5 5 l1-1 c1-1 2-1 2 0 l3 2 c1 1 1 3 0 4 l-1 1 c-2 2-7 0-11-4 s-6-9-4-11 z" fill="none" stroke="var(--white)" stroke-width="1.3"/>
    <!-- mail icon -->
    <circle cx="60" cy="308" r="15" fill="var(--red)"/>
    <rect x="52" y="302" width="16" height="12" fill="none" stroke="var(--white)" stroke-width="1.3"/>
    <polyline points="52,302 60,309 68,302" fill="none" stroke="var(--white)" stroke-width="1.3"/>
    <!-- globe icon -->
    <circle cx="60" cy="358" r="15" fill="var(--red)"/>
    <circle cx="60" cy="358" r="8" fill="none" stroke="var(--white)" stroke-width="1.3"/>
    <ellipse cx="60" cy="358" rx="3.5" ry="8" fill="none" stroke="var(--white)" stroke-width="1.1"/>
    <line x1="52" y1="358" x2="68" y2="358" stroke="var(--white)" stroke-width="1.1"/>
  </svg>

  <div class="name-banner">
    <p class="name-banner__name"><strong>Dario</strong> Whitcombe</p>
    <p class="name-banner__role">Principal</p>
  </div>

  <div class="firm-mark">
    <p class="firm-mark__name">Dario Whitcombe, CPA LLC</p>
    <p class="firm-mark__tagline">Certified Public Accountant</p>
  </div>

  <p class="contact contact--phone">+1 (555) 013-2074<br>+1 (555) 016-8459</p>
  <p class="contact contact--email">info@whitcombecpa.com</p>
  <p class="contact contact--web">www.whitcombecpa.com<br>www.whitcombe-tax-advisors.com</p>
</section>

<section class="card card--back" aria-label="Business card back">
  <svg class="card__shapes" width="744" height="430" viewBox="0 0 744 430" aria-hidden="true">
    <line x1="2" y1="395" x2="141" y2="395" stroke="var(--red)" stroke-width="1.2"/>
    <line x1="615" y1="395" x2="744" y2="395" stroke="var(--red)" stroke-width="1.2"/>
  </svg>
  <div class="firm-lockup">
    <p class="firm-lockup__name">Dario Whitcombe, CPA LLC</p>
    <p class="firm-lockup__tagline">Certified Public Accountant</p>
  </div>
  <p class="services">Accounting, Tax &amp; Consulting Services</p>
</section>

</body>
</html>
```